Pine leaf & Snapvista ad needed

I am in need of a simple static image ad to be used for Pineleaf & Snapvista. A photo of a nice roof on a nice house. "Instant Satellite Roof Estimates" "Your house, your time & instant estimate" . Our logo file is here: https://www.filecrate-example.net/share/q73kdm41xv9wpz2tbn8hs/JKsT4mWQpZ2xYcVn8bRfL6d?key=wm5tz81qvjx3c7bnd0ke9fa4r&v=0

Multiple variations will be purchased.

```html
<!DOCTYPE html>
<html lang="en">
<head>
<meta charset="utf-8">
<title>Instant Satellite Roof Estimates</title>
<link rel="stylesheet" href="https://fonts.googleapis.com/css2?family=Archivo:wght@500;600;700&display=swap">
<style>
  :root {
    --sky: #d5cacb;
    --sky-low: #cbbfbf;
    --haze: #a9a797;
    --tree: #5b6650;
    --roof: #33373c;
    --roof-light: #474b51;
    --stone: #b3a58f;
    --lawn: #5a8a3e;
    --lawn-deep: #43702f;
    --ink: #0b0b0b;
    --paper: #ffffff;
  }
  * { margin: 0; padding: 0; box-sizing: border-box; }
  html, body {
    width: 1200px;
    height: 1200px;
    overflow: hidden;
    background: var(--sky);
  }
  .ad {
    position: relative;
    width: 1200px;
    height: 1200px;
    overflow: hidden;
    background: var(--sky);
    font-family: "Archivo", Arial, sans-serif;
    color: var(--ink);
  }
  .house-photo {
    position: absolute;
    left: 0;
    top: 540px;
    width: 1200px;
    height: 660px;
    background: linear-gradient(180deg,
      var(--sky) 0%,
      var(--sky-low) 6%,
      var(--haze) 14%,
      var(--tree) 24%,
      var(--roof-light) 34%,
      var(--roof) 46%,
      var(--roof) 54%,
      var(--stone) 62%,
      #8d8676 70%,
      var(--lawn) 78%,
      var(--lawn-deep) 100%);
  }
  .brand {
    position: absolute;
    left: 46px;
    top: 46px;
    display: flex;
    align-items: center;
    gap: 16px;
  }
  .brand-mark {
    width: 24px;
    height: 24px;
    background: var(--ink);
  }
  .brand-name {
    font-weight: 500;
    font-size: 36px;
    line-height: 1.05;
    letter-spacing: 2px;
    text-transform: uppercase;
  }
  .headline {
    position: absolute;
    left: 46px;
    top: 174px;
    font-weight: 600;
    font-size: 96px;
    line-height: 108px;
    letter-spacing: 2.5px;
    white-space: nowrap;
  }
  .subhead {
    position: absolute;
    left: 50px;
    top: 434px;
    font-weight: 500;
    font-size: 52px;
    line-height: 57px;
    letter-spacing: 1px;
    white-space: nowrap;
  }
  .cta {
    position: absolute;
    left: 43px;
    top: 518px;
    width: 389px;
    height: 93px;
    background: var(--ink);
    color: var(--paper);
    border-radius: 8px;
    display: flex;
    align-items: center;
    justify-content: center;
    font-weight: 500;
    font-size: 33px;
    letter-spacing: 1px;
    white-space: nowrap;
  }
</style>
</head>
<body>
  <main class="ad">
    <div class="house-photo" role="img" aria-label="Aerial dusk photo of a stone ranch house with a dark standing-seam metal roof, lit windows, a small pool and green lawn, surrounded by trees"></div>

    <div class="brand">
      <span class="brand-mark"></span>
      <span class="brand-name">Hearthline<br>Roofing</span>
    </div>

    <h1 class="headline">Instant Satellite Roof<br>Estimates</h1>

    <p class="subhead">Your House, Your Time &amp; Instant Estimate</p>

    <div class="cta">Get Free Estimates</div>
  </main>
</body>
</html>
```